Business Card Design

We need a design for business cards for our company. We have a logo. We teach EMT's and we are based out of Virginia. The information that will need to add would be, name, title, phone number, email, address. On the back of the business card would be "We help you, help others"

Target Market(s)

People that want to become EMT's

Colors

Designer to choose colors to be used in the design.

Requirements
Must have
• company logo

```html
<!DOCTYPE html>
<html lang="en">
<head>
<meta charset="utf-8">
<title>MedicPath Training – Business Card</title>
<link href="https://fonts.googleapis.com/css2?family=Lato:wght@400;700;900&family=Montserrat:wght@300;500&display=swap" rel="stylesheet">
<style>
  :root {
    --stage: #2a2a2c;
    --card-navy: #1f2536;
    --card-navy-deep: #181d2b;
    --accent-red: #e8283c;
    --slate: #7f8b97;
    --text-light: #e9ecf1;
    --pattern-tone: #2e3748;
  }
  * { margin: 0; padding: 0; box-sizing: border-box; }
  html, body { width: 1200px; height: 900px; overflow: hidden; background: var(--stage); }
  .canvas { position: relative; width: 1200px; height: 900px; }

  .card {
    position: absolute; left: 250px; width: 700px; height: 400px;
    background: linear-gradient(135deg, var(--card-navy) 0%, var(--card-navy-deep) 100%);
    overflow: hidden; box-shadow: 0 18px 40px rgba(0,0,0,.55);
  }
  .card--back { top: 35px; }
  .card--front { top: 465px; }

  .cross-field {
    position: absolute; top: 0; right: 0; width: 300px; height: 400px;
    background: radial-gradient(ellipse at 70% 40%, var(--pattern-tone) 0%, rgba(46,55,72,0) 70%);
  }

  .brand { position: absolute; display: flex; align-items: center; gap: 12px; }
  .brand__dot { width: 18px; height: 18px; border-radius: 50%; background: var(--accent-red); }
  .brand__name {
    font-family: "Montserrat", sans-serif; font-weight: 500; color: var(--accent-red);
    letter-spacing: 1px; line-height: 1.05;
  }
  .card--back .brand { top: 50px; right: 60px; }
  .card--back .brand__name { font-size: 26px; }
  .card--front .brand { top: 95px; right: 80px; }
  .card--front .brand__name { font-size: 36px; }

  .tagline {
    position: absolute; left: 55px; bottom: 50px;
    font-family: "Montserrat", sans-serif; font-weight: 300; font-size: 22px;
    letter-spacing: 1px; color: var(--text-light);
  }

  .stethoscope-area {
    position: absolute; left: 0; top: 0; width: 250px; height: 200px;
    background: radial-gradient(ellipse at 40% 45%, #11141c 0%, rgba(17,20,28,0) 70%);
  }

  .contact { position: absolute; left: 55px; bottom: 80px; font-family: "Lato", sans-serif; color: var(--text-light); }
  .contact__name { font-size: 22px; color: var(--accent-red); letter-spacing: .5px; }
  .contact__name strong { font-weight: 900; }
  .contact__name span { font-weight: 400; }
  .contact__title { font-size: 15px; font-weight: 700; margin: 2px 0 8px; }
  .contact__row { display: flex; align-items: center; gap: 10px; font-size: 15px; margin-bottom: 4px; }
  .contact__row svg { width: 14px; height: 14px; fill: var(--accent-red); }
  .contact__web { font-size: 16px; font-weight: 700; color: var(--accent-red); margin-top: 2px; }

  .band { position: absolute; left: 0; bottom: 0; width: 700px; height: 100px; }
</style>
</head>
<body>
<div class="canvas">

  <section class="card card--back" aria-label="Card back">
    <div class="cross-field" role="img" aria-label="Faint medical cross pattern"></div>
    <div class="brand">
      <span class="brand__dot"></span>
      <span class="brand__name">MEDICPATH<br>TRAINING</span>
    </div>
    <p class="tagline">WE HELP YOU, HELP OTHERS</p>
  </section>

  <section class="card card--front" aria-label="Card front">
    <div class="cross-field" role="img" aria-label="Faint medical cross pattern"></div>
    <div class="stethoscope-area" role="img" aria-label="Photo of a black stethoscope"></div>
    <div class="brand">
      <span class="brand__dot"></span>
      <span class="brand__name">MEDICPATH<br>TRAINING</span>
    </div>

    <div class="contact">
      <p class="contact__name"><strong>DANA</strong> <span>HOLLOWAY</span></p>
      <p class="contact__title">Founder / Director</p>
      <p class="contact__row">
        <svg viewBox="0 0 24 24" aria-hidden="true"><path d="M6.6 10.8a15 15 0 0 0 6.6 6.6l2.2-2.2a1 1 0 0 1 1-.25 11.4 11.4 0 0 0 3.6.57 1 1 0 0 1 1 1V20a1 1 0 0 1-1 1A17 17 0 0 1 3 4a1 1 0 0 1 1-1h3.5a1 1 0 0 1 1 1c0 1.25.2 2.45.57 3.57a1 1 0 0 1-.25 1z"/></svg>
        +1 555 014 2273
      </p>
      <p class="contact__row">
        <svg viewBox="0 0 24 24" aria-hidden="true"><path d="M2 5h20v14H2z M2 5l10 8 10-8" fill="none" stroke="#e8283c" stroke-width="2"/></svg>
        info@medicpathtraining.com
      </p>
      <p class="contact__web">www.medicpathtraining.com</p>
    </div>

    <svg class="band" viewBox="0 0 700 100" aria-hidden="true">
      <path d="M0 82 H460 Q478 82 482 70 L488 56 H700 V100 H0 Z" fill="var(--slate)"/>
      <path d="M488 56 Q494 30 520 30 H700 V56 Z" fill="var(--accent-red)"/>
    </svg>
  </section>

</div>
</body>
</html>
```